Redesign of Grown Builder of BRIXO Weblog.

I'm an Grown Builder of BRIXO (GBOB), and I'm the person behind a small, off-the-beaten-path fan site, built using PageLoom.

The existing site is at http://quarvelnook.example. As you can see, it could use an infinitely better design!

My site was originally for reviews of BRIXO sets, and had extended to include general commentary and a small gallery of models I've built and a cast of characters. It's particularly known for my opinions and perspective on the world of BRIXO, and as such isn't necessarily child friendly.
While keeping existing content, the new version of the site will focus more on video content from my ClipHarbor channel.

In contrast to the current site, I'm looking for a light design that makes use of a few muted, low saturation colours, whilst remaining clean and relatively simple. The logo is part of the site's identity and should serve as inspiration for the design.
The content pages would keep the thin floating menu, and the content area would be no more than 1200 pixels wide.
Though it's a BRIXO fan site, I would like to avoid overt references to BRIXO elements. Other that that, you're more than welcome to use your creative license with the design.

In addition to the home, blog and post pages, I would also like a "placeholder" page that can be adapted for different page types. I will be building the theme from the designs, so don't worry about doing any coding.
You don't have to provide them all at once at this stage: I would suggest submitting either the home page or post page.

The final design should communicate "this is MY corner of the web", but above all else that it's about creativity and self-expression.

If you have any questions, please get in touch!
Updates

Target Market(s)

People interested in BRIXO in general, 12 and up.

Industry/Entity Type

Adult

Number of Pages Required

4 page

Font styles to use
Sans Serif
Decorative
Other font styles liked:
• Qhytsdakx

Requirements
Must have
• The tagline "Make It Yours".
• I'm keeping the font/fount used for headings (Qhytsdakx); I'm open to suggestions for the body text.
Should not have
• Overt references to BRIXO or BRIXO elements.

```html
<!DOCTYPE html>
<html lang="en">
<head>
<meta charset="utf-8">
<title>Quarvelnook — Grown Builder of BRIXO Weblog</title>
<link href="https://fonts.googleapis.com/css2?family=Oswald:wght@400;500;600&family=Open+Sans:wght@400;600;700&display=swap" rel="stylesheet">
<style>
:root{
  --ink:#2b2b2b;
  --ink-soft:#3a3a3a;
  --text:#7a7a7a;
  --muted:#a3a3a3;
  --line:#d9d9d9;
  --page:#f5f5f5;
  --band:#e8e8e8;
  --white:#ffffff;
  --footer:#262626;
  --footer-deep:#1d1d1d;
  --footer-text:#8d8d8d;
  --heading:"Oswald",sans-serif;
  --body:"Open Sans",sans-serif;
}
*{box-sizing:border-box;margin:0;padding:0}
html,body{width:1200px;height:2180px;overflow:hidden}
body{background:var(--page);font-family:var(--body);color:var(--text);font-size:12px;line-height:1.6;position:relative}
.wrap{width:880px;margin:0 auto;position:relative}
h1,h2,h3,h4{font-family:var(--heading);color:var(--ink);font-weight:500;text-transform:uppercase;letter-spacing:.5px}
.btn{display:inline-block;background:var(--ink);color:var(--white);font-family:var(--body);font-size:10px;font-weight:700;letter-spacing:.6px;padding:8px 14px;text-transform:uppercase;border-right:4px solid #5a5a5a}
.more{font-size:9px;font-weight:700;color:var(--ink);letter-spacing:.6px;text-transform:uppercase}
.media{display:block;background:linear-gradient(135deg,#bdbdbd,#8f8f8f)}

/* hero */
.hero{height:560px;background:radial-gradient(ellipse at 50% 40%,#fbfbfb 0%,#e9e9e9 55%,#d6d6d6 100%);position:relative}
.masthead{height:130px;position:relative}
.brand{position:absolute;left:0;top:0;display:flex;align-items:flex-end;gap:10px}
.brand-box{width:120px;height:100px;background:var(--ink);display:flex;align-items:flex-end;padding:12px}
.brand-name{font-family:var(--heading);font-size:24px;font-weight:600;color:var(--white);line-height:1;text-transform:lowercase}
.phone{position:absolute;right:0;top:14px;display:flex;gap:8px;align-items:center;font-size:10px;color:var(--text)}
.phone strong{display:block;color:var(--ink);font-size:11px}
.nav{position:absolute;right:0;top:74px;display:flex;gap:24px;font-family:var(--heading);font-size:13px;color:var(--ink);letter-spacing:.8px}
.hero-body{display:flex;justify-content:space-between;margin-top:50px}
.intro{width:380px;padding-top:40px}
.intro h1{font-size:30px;margin-bottom:16px}
.intro p{margin-bottom:14px}
.video{width:448px;height:320px;position:relative;border:4px solid var(--white);box-shadow:0 2px 8px rgba(0,0,0,.15);background:linear-gradient(160deg,#9fa6ad,#6d6f74 60%,#4a4b4f)}
.video-bar{position:absolute;left:0;right:0;bottom:0;height:30px;background:rgba(20,20,20,.85)}
.video-play{position:absolute;left:50%;top:50%;width:64px;height:44px;margin:-22px 0 0 -32px;background:rgba(20,20,20,.8);border-radius:6px}
.arrow{position:absolute;top:310px;width:34px;height:34px;border-radius:50%;background:#9a9a9a;display:flex;align-items:center;justify-content:center}
.arrow.left{left:40px}.arrow.right{right:40px}

/* section heads */
.section-head{display:flex;align-items:flex-start;justify-content:space-between;border-top:1px solid var(--line);padding-top:14px;margin-bottom:22px}
.section-head .title{border-left:4px solid var(--ink);padding-left:10px}
.section-head h2{font-size:20px;line-height:1.1}
.section-head p{font-size:10px;color:var(--muted);font-style:italic}
.pager{display:flex;gap:6px;padding-top:4px}

/* commentary */
.commentary{padding-top:28px;height:420px}
.cards{display:flex;justify-content:space-between}
.card{width:280px}
.card .media{height:140px;margin-bottom:14px}
.card h3{font-size:12px;margin-bottom:8px}
.card p{font-size:10.5px;margin-bottom:10px}

/* reviews */
.reviews{background:var(--band);height:540px;padding-top:22px}
.reviews .section-head{border-top-color:#cfcfcf}
.review-grid{display:flex;justify-content:space-between}
.feature{width:530px;height:390px;position:relative}
.feature .media{height:100%;background:linear-gradient(150deg,#c9c9c4,#a7a8a3 50%,#7f807c)}
.feature-cap{position:absolute;left:0;right:0;bottom:0;height:82px;background:rgba(35,35,35,.82);padding:14px 18px;color:#cfcfcf;font-size:10.5px}
.feature-cap .date{color:var(--white);font-weight:700;font-size:11px;margin-bottom:4px;display:block}
.review-list{width:332px;display:flex;flex-direction:column;justify-content:space-between;height:390px}
.review-item{display:flex;gap:14px;height:118px}
.review-item .media{width:110px;height:118px;flex:none}
.review-item .date{display:inline-block;background:#7b7b7b;color:var(--white);font-size:9.5px;font-weight:700;padding:2px 8px;margin-bottom:6px}
.review-item p{font-size:10.5px}

/* three columns */
.trio{padding-top:24px;height:360px}
.trio-cols{display:flex;justify-content:space-between}
.trio-col{width:280px}
.trio-col .section-head{margin-bottom:14px}
.trio-col .media{height:130px;margin-bottom:12px}
.trio-col h3{font-size:12px;margin-bottom:6px}
.trio-col p{font-size:10.5px;margin-bottom:8px}

/* footer */
.footer{position:absolute;left:0;right:0;top:1860px;height:320px;background:var(--footer);color:var(--footer-text)}
.footer-cols{display:flex;justify-content:space-between;padding-top:32px}
.footer h4{color:#d8d8d8;font-size:13px;margin-bottom:16px}
.photos{width:260px;display:grid;grid-template-columns:repeat(4,52px);gap:10px}
.photos .media{height:52px;background:linear-gradient(135deg,#6b6b6b,#454545)}
.tweets{width:290px}
.tweet{display:flex;gap:10px;font-size:10.5px;margin-bottom:14px}
.partners{width:240px}
.badge{width:180px;height:56px;background:#e9e9e9;border-radius:3px}
.footer-bottom{position:absolute;left:0;right:0;bottom:0;height:70px;background:var(--footer-deep)}
.footer-bottom .wrap{display:flex;align-items:center;justify-content:space-between;height:70px}
.socials{display:flex;gap:8px}
.socials span{width:24px;height:24px;border-radius:50%;border:2px solid #777;display:block}
.foot-brand{display:flex;align-items:center;gap:8px;font-family:var(--heading);font-weight:600;font-size:16px;color:#d8d8d8;text-transform:lowercase}
.foot-brand i{width:14px;height:14px;background:#d8d8d8;display:block}
.legal{font-size:9.5px;text-align:right;width:340px}
</style>
</head>
<body>

<header class="hero">
  <div class="wrap">
    <div class="masthead">
      <div class="brand">
        <div class="brand-box"><span class="brand-name">quarvelnook</span></div>
      </div>
      <div class="phone">
        <svg width="16" height="16" viewBox="0 0 16 16"><rect width="16" height="16" rx="2" fill="#2b2b2b"/><path d="M5 4h2l1 2.5-1.3.8a5 5 0 0 0 2 2l.8-1.3L12 9v2a1 1 0 0 1-1 1A7 7 0 0 1 4 5a1 1 0 0 1 1-1z" fill="#fff"/></svg>
        <div>Phone<strong>0800 555 0199</strong></div>
      </div>
      <nav class="nav"><span>COMMENTARY</span><span>REVIEWS</span><span>MOCS</span><span>CAST</span><span>ABOUT</span><span>CONTACT</span></nav>
    </div>
    <div class="hero-body">
      <div class="intro">
        <h1>Welcome to Quarvelnook</h1>
        <p>One builder's corner of the web, full of opinions, reviews and odd little creations. Pull up a chair and stay for a while, the kettle is on.</p>
        <p>Fresh videos land every week on the channel, with build logs, set breakdowns and the occasional rant about the hobby and its many quirks.</p>
        <span class="btn">Read more</span>
      </div>
      <div class="video" role="img" aria-label="Embedded video of a brick-built diorama scene">
        <span class="video-play"></span>
        <span class="video-bar"></span>
      </div>
    </div>
  </div>
  <span class="arrow left"><svg width="10" height="12" viewBox="0 0 10 12"><path d="M8 1 2 6l6 5" stroke="#fff" stroke-width="2" fill="none"/></svg></span>
  <span class="arrow right"><svg width="10" height="12" viewBox="0 0 10 12"><path d="m2 1 6 5-6 5" stroke="#fff" stroke-width="2" fill="none"/></svg></span>
</header>

<section class="commentary">
  <div class="wrap">
    <div class="section-head">
      <div class="title"><h2>Commentary</h2><p>Get your fix for thoughts, opinions, rants and ravings on the world of BRIXO</p></div>
      <div class="pager"><svg width="26" height="10" viewBox="0 0 26 10"><path d="M6 1 2 5l4 4M20 1l4 4-4 4" stroke="#888" stroke-width="2" fill="none"/></svg></div>
    </div>
    <div class="cards">
      <article class="card">
        <span class="media" role="img" aria-label="Photo of a colourful brick-built window display"></span>
        <h3>Harbor Windows at Stud Expo 2015</h3>
        <p>A walk through the shop window displays, with notes on the clever parts use and a few builds that deserve a much closer look.</p>
        <span class="more">Read more ›</span>
      </article>
      <article class="card">
        <span class="media" role="img" aria-label="Photo of small figures posed in a row"></span>
        <h3>Harbor Windows at Stud Expo 2015</h3>
        <p>A walk through the shop window displays, with notes on the clever parts use and a few builds that deserve a much closer look.</p>
        <span class="more">Read more ›</span>
      </article>
      <article class="card">
        <span class="media" role="img" aria-label="Photo of costumed figures lined up"></span>
        <h3>Harbor Windows at Stud Expo 2015</h3>
        <p>A walk through the shop window displays, with notes on the clever parts use and a few builds that deserve a much closer look.</p>
        <span class="more">Read more ›</span>
      </article>
    </div>
  </div>
</section>

<section class="reviews">
  <div class="wrap">
    <div class="section-head">
      <div class="title"><h2>Reviews</h2></div>
    </div>
    <div class="review-grid">
      <div class="feature">
        <span class="media" role="img" aria-label="Photo of a built set in a bright room"></span>
        <div class="feature-cap"><span class="date">Feb 15, 2015</span>An honest look at the new modular set, from the bag order to the finished build and how it sits on the shelf.</div>
      </div>
      <div class="review-list">
        <div class="review-item"><span class="media" role="img" aria-label="Photo of a small built vehicle"></span><div><span class="date">Feb 15, 2015</span><p>A short review of the latest small vehicle pack, with thoughts on value, parts and playability for grown builders.</p></div></div>
        <div class="review-item"><span class="media" role="img" aria-label="Photo of a figure close-up"></span><div><span class="date">Feb 15, 2015</span><p>A short review of the latest small vehicle pack, with thoughts on value, parts and playability for grown builders.</p></div></div>
        <div class="review-item"><span class="media" role="img" aria-label="Photo of a built scene"></span><div><span class="date">Feb 15, 2015</span><p>A short review of the latest small vehicle pack, with thoughts on value, parts and playability for grown builders.</p></div></div>
      </div>
    </div>
  </div>
</section>

<section class="trio">
  <div class="wrap trio-cols">
    <div class="trio-col">
      <div class="section-head"><div class="title"><h2>MOCs</h2><p>Built by my own hands</p></div><div class="pager"><svg width="26" height="10" viewBox="0 0 26 10"><path d="M6 1 2 5l4 4M20 1l4 4-4 4" stroke="#888" stroke-width="2" fill="none"/></svg></div></div>
      <span class="media" role="img" aria-label="Photo of a custom brick-built model"></span>
      <h3>Harbor Windows at Stud Expo 2015</h3>
      <p>Notes from the build table on a new creation, with the odd trick and a few parts that made it all come together.</p>
      <span class="more">Read more ›</span>
    </div>
    <div class="trio-col">
      <div class="section-head"><div class="title"><h2>Features</h2><p>Built by my own hands</p></div><div class="pager"><svg width="26" height="10" viewBox="0 0 26 10"><path d="M6 1 2 5l4 4M20 1l4 4-4 4" stroke="#888" stroke-width="2" fill="none"/></svg></div></div>
      <span class="media" role="img" aria-label="Photo of a group of small figures"></span>
      <h3>Harbor Windows at Stud Expo 2015</h3>
      <p>Notes from the build table on a new creation, with the odd trick and a few parts that made it all come together.</p>
      <span class="more">Read more ›</span>
    </div>
    <div class="trio-col">
      <div class="section-head"><div class="title"><h2>Cast</h2><p>Built by my own hands</p></div><div class="pager"><svg width="26" height="10" viewBox="0 0 26 10"><path d="M6 1 2 5l4 4M20 1l4 4-4 4" stroke="#888" stroke-width="2" fill="none"/></svg></div></div>
      <span class="media" role="img" aria-label="Photo of a character figure on an orange backdrop" style="background:linear-gradient(135deg,#e08a4a,#c4622a)"></span>
      <h3>Harbor Windows at Stud Expo 2015</h3>
      <p>Notes from the build table on a new creation, with the odd trick and a few parts that made it all come together.</p>
      <span class="more">Read more ›</span>
    </div>
  </div>
</section>

<footer class="footer">
  <div class="wrap footer-cols">
    <div>
      <h4>Snapwell Photostream</h4>
      <div class="photos">
        <span class="media" role="img" aria-label="Photostream thumbnail"></span><span class="media" role="img" aria-label="Photostream thumbnail"></span><span class="media" role="img" aria-label="Photostream thumbnail"></span><span class="media" role="img" aria-label="Photostream thumbnail"></span>
        <span class="media" role="img" aria-label="Photostream thumbnail"></span><span class="media" role="img" aria-label="Photostream thumbnail"></span><span class="media" role="img" aria-label="Photostream thumbnail"></span><span class="media" role="img" aria-label="Photostream thumbnail"></span>
      </div>
    </div>
    <div class="tweets">
      <h4>@quarvelnook1</h4>
      <div class="tweet"><svg width="12" height="12" viewBox="0 0 12 12"><rect width="12" height="12" rx="2" fill="#555"/></svg><p>Just posted a new build log, a long one this time with plenty of photos and far too many opinions.</p></div>
      <div class="tweet"><svg width="12" height="12" viewBox="0 0 12 12"><rect width="12" height="12" rx="2" fill="#555"/></svg><p>New video is up on the channel, a full review of the spring sets with my usual honest take.</p></div>
    </div>
    <div class="partners">
      <h4>Partners</h4>
      <div class="badge" role="img" aria-label="Partner badge"></div>
    </div>
  </div>
  <div class="footer-bottom">
    <div class="wrap">
      <div class="socials"><span></span><span></span><span></span><span></span><span></span></div>
      <div class="foot-brand"><i></i>quarvelnook</div>
      <p class="legal">Copyright 2015 Quarvelnook. All rights reserved.<br>BRIXO is a trademark of its owners, who do not sponsor this site.</p>
    </div>
  </div>
</footer>

</body>
</html>
```